Lantern Petals Website v.1 - attract floral shop franchisees

I need a simple information website for my new business. We are a franchisor of flower shops. The overall purpose of the website is to promote the company and the service, especially to potential franchisees and retailers. Only about 4 pages are required including homepage, About, For Supermarkets, For Franchisees, and Contact. No special functions are required except the site will have two separate inquiry forms that must be filled out online and submitted via automated email. Similarly, an email form should be linked from the Contact page. I have a logo and business cards designed by ArtMingle, and I would like the site to have a consistent color scheme and style. The key to design will be to express the joy and love associated with flowers and floral bouquets.
IMPORTANT - I will be exporting the website design to Wordpress CMS in a site hosted by HostNimbus. For smooth integration into WordPress hosted by HostNimbus, the designer should build the site using a WordPress-friendly format. Ideally, they should use HTML, CSS, and PHP. Creating a custom theme or using a page builder that exports to WordPress-compatible files is best. This ensures the site can be easily imported and managed within WordPress.

Target Market(s)

Potential franchisees (existing florists or creative types who might like to own a floral business) and supermarkets who might want us to run their floral department

Industry/Entity Type

Floral retailing

Requirements
Must have
• A brand theme that is beautiful, consistent throughout and builds on the logo design
Nice to have
• Show gender and ethnic diversity in customers and florists. Pictures of happy florists (for franchisees) and pictures of amazing floral department displays (for supermarkets)

```html
<!DOCTYPE html>
<html lang="en">
<head>
<meta charset="utf-8">
<title>Lantern Petals</title>
<link href="https://fonts.googleapis.com/css2?family=Poppins:wght@400;500;600;700;800&family=Yellowtail&display=swap" rel="stylesheet">
<style>
:root{
  --cream:#fcf5ec;
  --green:#04873e;
  --green-dark:#036b31;
  --gold:#f0b12f;
  --gold-deep:#e9a61d;
  --ink:#5f5f5f;
  --night:#2a2a2a;
  --white:#ffffff;
}
*{margin:0;padding:0;box-sizing:border-box}
html,body{width:1200px;height:3911px;overflow:hidden;background:var(--cream)}
body{font-family:'Poppins',sans-serif;color:var(--ink)}
.page{position:relative;width:1200px;height:3911px;overflow:hidden;background:var(--cream)}
.abs{position:absolute}
.script{font-family:'Yellowtail',cursive;color:var(--gold);font-weight:400}
.btn{position:absolute;display:flex;align-items:center;justify-content:center;border-radius:20px;font-weight:700;font-size:14px;text-transform:uppercase;letter-spacing:.2px}
.btn-green{background:var(--green);color:var(--gold)}
.btn-gold{background:var(--gold);color:var(--green)}

.brand{position:absolute;left:116px;top:48px;display:flex;align-items:center;gap:14px}
.brand-dot{width:46px;height:46px;border-radius:50%;background:var(--gold)}
.brand-name{font-size:34px;font-weight:600;color:var(--green)}
.contact{position:absolute;top:24px;display:flex;align-items:center;gap:16px}
.contact-hex{width:52px;height:56px}
.contact small{display:block;font-size:11px;font-weight:600;color:var(--green)}
.contact strong{display:block;font-size:19px;font-weight:700;color:var(--green)}
.navbar{position:absolute;left:448px;top:100px;width:752px;height:57px;background:var(--green);clip-path:polygon(38px 0,100% 0,100% 100%,0 100%)}
.nav{position:absolute;top:100px;height:57px;display:flex;align-items:center;left:531px;gap:46px}
.nav a{color:var(--white);font-size:15px;font-weight:500;text-decoration:none}

.hero-photo{position:absolute;left:0;top:160px;width:1200px;height:640px;background:radial-gradient(circle at 55% 45%,#b24a4a 0,#7a2c33 25%,#4d3a2e 55%,#2e2a22 100%)}
.hero-title{position:absolute;left:0;width:1200px;top:322px;text-align:center;font-family:'Yellowtail',cursive;font-size:104px;color:var(--white)}
.hero-sub{position:absolute;left:0;width:1200px;top:447px;text-align:center;color:var(--white);font-size:23px;line-height:42px}

.about-bg{position:absolute;left:0;top:760px;width:1200px;height:820px;background:radial-gradient(ellipse at 25% 40%,#efe6dc 0,var(--cream) 60%)}
.mark{position:absolute;left:212px;top:1010px;width:330px;height:330px;border-radius:50%;border:16px solid var(--gold);display:flex;align-items:center;justify-content:center}
.mark span{font-size:34px;font-weight:600;color:var(--green)}
.label{position:absolute;font-size:38px}
.h2{position:absolute;font-size:44px;font-weight:800;color:var(--green);letter-spacing:.5px;text-transform:uppercase}
.para{position:absolute;font-size:15.5px;line-height:31.5px}
.para-light{color:var(--white)}

.green-section{position:absolute;left:0;top:1640px;width:1200px;height:707px;background:var(--green)}

.touch{position:absolute;left:0;top:3129px;width:1200px;height:420px;background:var(--gold)}
.touch-center{position:absolute;left:0;width:1200px;text-align:center}

.footer{position:absolute;left:0;top:3520px;width:1200px;height:391px;background:var(--night)}
.fnav{position:absolute;top:3752px;left:0;width:1200px;display:flex;justify-content:center;gap:36px}
.fnav a{color:var(--white);font-size:15px;font-weight:500;text-decoration:none}
.social{position:absolute;top:3798px;left:522px;display:flex;gap:16px}
.copy{position:absolute;top:3858px;left:0;width:1200px;text-align:center;font-size:11px;color:var(--white)}
.stripe{position:absolute;left:0;top:3901px;width:1200px;height:10px;background:linear-gradient(var(--green) 0 50%,var(--gold) 50% 100%)}
</style>
</head>
<body>
<div class="page">

  <div class="brand">
    <div class="brand-dot"></div>
    <div class="brand-name">Lantern Petals</div>
  </div>
  <div class="contact" style="left:534px">
    <svg class="contact-hex" viewBox="0 0 52 56"><polygon points="26,0 52,14 52,42 26,56 0,42 0,14" fill="#f0b12f"/><path d="M19 17c2-1 4 0 5 3l-2 3c1 3 4 6 7 7l3-2c3 1 4 3 3 5-2 3-5 3-9 1-4-2-8-6-10-10-2-4-1-6 3-7z" fill="#04873e"/></svg>
    <div><small>CALL US:</small><strong>+1 555 310 0142</strong></div>
  </div>
  <div class="contact" style="left:790px">
    <svg class="contact-hex" viewBox="0 0 52 56"><polygon points="26,0 52,14 52,42 26,56 0,42 0,14" fill="#f0b12f"/><rect x="15" y="19" width="22" height="17" rx="2" fill="#04873e"/><path d="M15 21l11 8 11-8" stroke="#f0b12f" stroke-width="2" fill="none"/></svg>
    <div><small>EMAIL US:</small><strong>hello@lanternpetals.com</strong></div>
  </div>
  <div class="navbar"></div>
  <nav class="nav">
    <a>ABOUT US</a><a>FOR SUPERMARKETS</a><a>FOR FRANCHISEES</a><a>CONTACT US</a>
  </nav>

  <div class="hero-photo" role="img" aria-label="Close-up of a lush mixed bouquet with roses, lilies and berries"></div>
  <div class="hero-title">Lantern Petals</div>
  <p class="hero-sub">Fresh flowers convey beauty and love, and in our view should become<br>something every person regularly enjoys.</p>
  <div class="btn btn-gold" style="left:454px;top:553px;width:134px;height:37px">Get Started</div>
  <div class="btn btn-green" style="left:611px;top:553px;width:134px;height:37px">Contact Us</div>

  <div class="about-bg" role="img" aria-label="Faint background of soft white flowers"></div>
  <svg class="abs" style="left:0;top:680px" width="1200" height="130" viewBox="0 0 1200 130" preserveAspectRatio="none">
    <path d="M0 80 C180 0 420 10 700 70 C900 110 1080 90 1200 60 L1200 130 L0 130Z" fill="#f0b12f"/>
    <path d="M0 120 C120 60 300 40 460 80 C300 60 120 80 0 130Z" fill="#04873e"/>
    <path d="M0 130 C220 70 520 90 820 112 C1000 122 1120 100 1200 76 L1200 130Z" fill="#fcf5ec"/>
  </svg>

  <div class="mark" role="img" aria-label="Lantern Petals brand mark area"><span>Lantern Petals</span></div>
  <div class="label script" style="left:653px;top:898px">About Us</div>
  <div class="h2" style="left:653px;top:946px">Who We Are</div>
  <p class="para" style="left:653px;top:1022px;width:440px">Fresh flowers convey beauty and love, and in our view should become something every person regularly enjoys. Lantern Petals is an entrepreneurial company created to make top quality fresh flowers and professionally-designed bouquets accessible to every consumer at affordable prices.</p>
  <p class="para" style="left:653px;top:1243px;width:440px">Professional florists typically sell the finest quality stems, design the most beautiful bouquets and provide the finest customer service, but their costs – of floral products, retail spaces</p>
  <div class="btn btn-green" style="left:653px;top:1400px;width:122px;height:35px;font-size:13px">Read More</div>

  <div class="green-section" role="img" aria-label="Green-tinted background of florist tools"></div>
  <svg class="abs" style="left:0;top:1580px" width="1200" height="120" viewBox="0 0 1200 120" preserveAspectRatio="none">
    <path d="M0 60 C260 10 520 0 800 40 C980 66 1110 40 1200 0 L1200 120 L0 120Z" fill="#f0b12f"/>
    <path d="M760 60 C950 80 1100 50 1200 20 L1200 40 C1100 80 950 90 760 60Z" fill="#04873e"/>
    <path d="M0 80 C300 40 560 50 820 96 C980 116 1110 80 1200 50 L1200 120 L0 120Z" fill="#04873e"/>
  </svg>
  <div class="label script" style="left:112px;top:1780px">Lantern</div>
  <div class="h2" style="left:110px;top:1830px;color:var(--white)">For Supermarkets</div>
  <p class="para para-light" style="left:113px;top:1905px;width:440px">Lantern Petals works with some of the country's largest and most progressive supermarkets to provide franchisee ownership and operation of their strategically important floral departments.  Supermarkets find that Lantern Petals is able to improve their financial outcomes, provide attentive customer service and satisfaction, and lift the quality of the entire store environment.</p>
  <div class="btn btn-gold" style="left:113px;top:2184px;width:122px;height:35px;font-size:13px">Read More</div>
  <svg class="abs" style="left:590px;top:1770px" width="510" height="470" viewBox="0 0 510 470">
    <defs>
      <linearGradient id="pink" x1="0" y1="0" x2="1" y2="1"><stop offset="0" stop-color="#f2c0c8"/><stop offset="1" stop-color="#8e9a6a"/></linearGradient>
      <linearGradient id="orange" x1="0" y1="0" x2="1" y2="1"><stop offset="0" stop-color="#f7a43a"/><stop offset="1" stop-color="#e07a1e"/></linearGradient>
      <linearGradient id="mixed" x1="0" y1="0" x2="1" y2="1"><stop offset="0" stop-color="#e8dfd8"/><stop offset="1" stop-color="#c7537c"/></linearGradient>
      <linearGradient id="red" x1="0" y1="0" x2="1" y2="1"><stop offset="0" stop-color="#d11f2b"/><stop offset="1" stop-color="#8d1119"/></linearGradient>
      <linearGradient id="plum" x1="0" y1="0" x2="1" y2="1"><stop offset="0" stop-color="#d7d2d4"/><stop offset="1" stop-color="#7b3a5a"/></linearGradient>
      <linearGradient id="amber" x1="0" y1="0" x2="1" y2="1"><stop offset="0" stop-color="#6d5a2a"/><stop offset="1" stop-color="#d98a2a"/></linearGradient>
      <linearGradient id="sage" x1="0" y1="0" x2="1" y2="1"><stop offset="0" stop-color="#3e4a44"/><stop offset="1" stop-color="#b5a99a"/></linearGradient>
    </defs>
    <g role="img" aria-label="Florist holding pink tulips"><polygon points="172,6 241,46 241,126 172,166 103,126 103,46" fill="url(#pink)"/></g>
    <g role="img" aria-label="Orange rose bouquet"><polygon points="338,6 407,46 407,126 338,166 269,126 269,46" fill="url(#orange)"/></g>
    <g role="img" aria-label="Woman smelling a mixed bouquet"><polygon points="86,152 155,192 155,272 86,312 17,272 17,192" fill="url(#mixed)"/></g>
    <g role="img" aria-label="Red roses bouquet"><polygon points="253,152 322,192 322,272 253,312 184,272 184,192" fill="url(#red)" stroke="#f0b12f" stroke-width="8"/></g>
    <g role="img" aria-label="Purple and burgundy arrangement"><polygon points="422,152 491,192 491,272 422,312 353,272 353,192" fill="url(#plum)"/></g>
    <g role="img" aria-label="Autumn floral arrangement"><polygon points="166,298 235,338 235,418 166,458 97,418 97,338" fill="url(#amber)"/></g>
    <g role="img" aria-label="Florist arranging stems"><polygon points="335,298 404,338 404,418 335,458 266,418 266,338" fill="url(#sage)"/></g>
  </svg>

  <div class="abs" style="left:112px;top:2488px;width:488px;height:542px;border-radius:20px;background:linear-gradient(160deg,#d9c7b8 0,#b8a6d8 45%,#7da0d6 70%,#e9a7c4 100%);box-shadow:0 10px 24px rgba(0,0,0,.15)" role="img" aria-label="Smiling florist holding a large pastel bouquet"></div>
  <div class="label script" style="left:687px;top:2548px">Lantern</div>
  <div class="h2" style="left:685px;top:2598px">For Franchisees</div>
  <p class="para" style="left:687px;top:2670px;width:410px;line-height:34px">Lantern Petals brings the best of professional florists and supermarkets together for the benefit of consumers.  It supports a national network of owner-operator franchisees, who in many cases are multi-site professional florists, with comprehensive services to enhance franchise profitability.  Lantern Petals works with some of the country's</p>
  <div class="btn btn-green" style="left:687px;top:2928px;width:122px;height:35px;font-size:13px">Read More</div>

  <div class="touch" role="img" aria-label="Gold-tinted background of flowers"></div>
  <div class="touch-center script" style="top:3182px;font-size:36px;color:var(--white)">Lantern</div>
  <div class="touch-center" style="top:3232px;font-size:43px;font-weight:800;color:var(--white)">GET IN TOUCH WITH US</div>
  <div class="touch-center" style="top:3296px;font-size:18px;color:var(--white)">For questions and further information, contact info@lantern-petals.com</div>
  <div class="btn btn-green" style="left:246px;top:3347px;width:308px;height:37px;font-size:13px">New Florist Franchise Inquiry</div>
  <div class="btn btn-green" style="left:585px;top:3347px;width:367px;height:37px;font-size:13px">Professional Florist Franchise Inquiry</div>

  <div class="footer"></div>
  <svg class="abs" style="left:0;top:3440px" width="1200" height="130" viewBox="0 0 1200 130" preserveAspectRatio="none">
    <path d="M0 90 C200 40 420 30 640 50 C860 70 1040 60 1200 20 L1200 130 L0 130Z" fill="#04873e"/>
    <path d="M0 110 C240 60 500 60 760 80 C960 95 1100 70 1200 50 L1200 70 C1100 100 960 110 760 100 C500 80 240 90 0 130Z" fill="#ffffff"/>
    <path d="M0 120 C240 80 520 80 760 100 C960 115 1100 90 1200 70 L1200 130 L0 130Z" fill="#2a2a2a"/>
    <path d="M460 98 C640 98 820 110 1000 100 C840 118 640 112 460 98Z" fill="#f0b12f"/>
  </svg>
  <div class="abs" style="left:0;top:3648px;width:1200px;display:flex;justify-content:center;align-items:center;gap:14px">
    <div style="width:44px;height:44px;border-radius:50%;background:var(--gold)"></div>
    <div style="font-size:34px;font-weight:600;color:var(--gold)">Lantern Petals</div>
  </div>
  <nav class="fnav"><a>HOME</a><a>ABOUT US</a><a>FOR SUPERMARKETS</a><a>FOR FRANCHISEES</a><a>CONTACT US</a></nav>
  <div class="social">
    <svg width="42" height="44" viewBox="0 0 42 44"><polygon points="21,0 42,11 42,33 21,44 0,33 0,11" fill="#f0b12f"/></svg>
    <svg width="42" height="44" viewBox="0 0 42 44"><polygon points="21,0 42,11 42,33 21,44 0,33 0,11" fill="#f0b12f"/></svg>
    <svg width="42" height="44" viewBox="0 0 42 44"><polygon points="21,0 42,11 42,33 21,44 0,33 0,11" fill="#f0b12f"/></svg>
  </div>
  <div class="copy">(C) Copyright 2024 | All Rights Reserved</div>
  <div class="stripe"></div>
</div>
</body>
</html>
```